Stationery and Business Card Design

We need stationary design for our new company lanternfold. Lanternfold is a company that provides city apartment rentals for tourists in Athens We need business cards, letterheads for A4 and A5 and envelopes for A4 A5. The design needs to be modern, friendly and corporate.

Target Market(s)

City Tourists

Industry/Entity Type

Tourism

```html
<!DOCTYPE html>
<html lang="en">
<head>
<meta charset="utf-8">
<title>Lanternfold Business Card</title>
<link href="https://fonts.googleapis.com/css2?family=Raleway:wght@400;500;600&display=swap" rel="stylesheet">
<style>
  :root {
    --backdrop: #a8a6a7;
    --plum: #85205a;
    --plum-dark: #761c50;
    --paper: #f2f2f2;
    --charcoal: #3b3837;
    --ink: #333031;
    --white: #ffffff;
  }
  * { margin: 0; padding: 0; box-sizing: border-box; }
  html, body {
    width: 1200px; height: 1200px; overflow: hidden;
    background: var(--backdrop);
    font-family: "Raleway", sans-serif;
  }
  .card {
    position: absolute;
    border-radius: 22px;
    overflow: hidden;
  }
  .card-front {
    left: 238px; top: 118px; width: 713px; height: 419px;
    background: var(--plum);
  }
  .card-back {
    left: 231px; top: 645px; width: 712px; height: 415px;
    background: var(--paper);
  }
  .brand-square {
    position: absolute;
  }
  .card-front .brand-square {
    left: 302px; top: 113px; width: 102px; height: 99px;
    background: var(--white);
  }
  .card-front .brand-name {
    position: absolute; left: 0; right: 0; top: 212px;
    text-align: center;
    color: var(--white);
    font-size: 62px; font-weight: 400; letter-spacing: -1px;
  }
  .wave {
    position: absolute; left: 0; top: 0;
  }
  .card-back .brand-square {
    left: 145px; top: 93px; width: 92px; height: 90px;
    background: var(--plum);
  }
  .card-back .brand-name {
    position: absolute; left: 36px; top: 190px;
    color: var(--plum);
    font-size: 54px; font-weight: 400; letter-spacing: -1px;
  }
  .holder {
    position: absolute; right: 36px; top: 44px;
    text-align: right; color: var(--white);
  }
  .holder-name { font-size: 25px; font-weight: 600; }
  .holder-title { font-size: 18px; font-weight: 400; margin-top: 4px; }
  .contacts {
    position: absolute; left: 40px; top: 302px;
    list-style: none; color: var(--ink);
    font-size: 18px;
  }
  .contacts li {
    display: flex; align-items: center; height: 24px;
  }
  .contacts svg { width: 16px; height: 14px; margin-right: 18px; fill: var(--plum); }
  .contacts .accent { color: var(--plum); }
  .address {
    position: absolute; right: 40px; top: 328px;
    text-align: right; color: var(--ink);
    font-size: 18px; line-height: 25px;
  }
</style>
</head>
<body>

<section class="card card-front">
  <div class="brand-square"></div>
  <div class="brand-name">Lanternfold</div>
</section>

<section class="card card-back">
  <svg class="wave" width="712" height="415" viewBox="0 0 712 415" aria-hidden="true">
    <path fill="var(--plum)" d="M0,0 H712 V168 C610,150 540,90 420,52 C280,10 110,10 0,38 Z"/>
    <path fill="var(--charcoal)" d="M0,40 C110,12 280,12 420,54 C540,92 610,152 712,170 V192 C600,178 530,120 420,82 C300,42 140,32 0,62 Z"/>
    <path fill="var(--paper)" d="M60,55 C180,30 320,36 420,68 C520,100 600,160 712,180 V184 C600,166 520,108 420,74 C320,42 180,36 60,55 Z"/>
  </svg>

  <div class="holder">
    <div class="holder-name">Nikos Andreou</div>
    <div class="holder-title">Your Title</div>
  </div>

  <div class="brand-square"></div>
  <div class="brand-name">Lanternfold</div>

  <ul class="contacts">
    <li>
      <svg viewBox="0 0 16 14"><path d="M1,4 C1,1 15,1 15,4 L12,5 L11,3 H5 L4,5 Z M3,6 H13 L15,13 H1 Z"/></svg>
      +00 111 222 3333
    </li>
    <li>
      <svg viewBox="0 0 16 14"><circle cx="8" cy="7" r="6.5" fill="none" stroke="var(--plum)" stroke-width="1.5"/><path d="M1.5,7 H14.5 M8,0.5 V13.5" stroke="var(--plum)" stroke-width="1.2"/><ellipse cx="8" cy="7" rx="3" ry="6.5" fill="none" stroke="var(--plum)" stroke-width="1.2"/></svg>
      www.<span class="accent">yourwebsite</span>.com
    </li>
    <li>
      <svg viewBox="0 0 16 14"><path d="M0,2 H16 V12 H0 Z M1.5,3.5 L8,8.5 L14.5,3.5" fill="var(--plum)" stroke="var(--paper)" stroke-width="1.2"/></svg>
      yourname@yourwebsite.com
    </li>
  </ul>

  <div class="address">
    Your Long Commercial<br>or business address
  </div>
</section>

</body>
</html>
```